Building company buisness cards

We are looking for a sharp modern new look for our business cards.We are a New Zealand based company that specialises in house and land packages.We have attached a photo of the current logo and would like to see if it can be improved somehow if needed.We are open to any colours but we have chosen Black and White at this stage. Feel free to change the font and make the logo smarter looking.Play with the colours and see what looks best.We want a card that looks so good know one will want to throw it away!

Target Market(s)

Building profesonals, home buyers

Industry/Entity Type

Building

Contact Information for Business Card

Garrick Tenwood
0275390628
garrickt@hartvale.co.nz

Font styles to use
Serif
Sans Serif

Colors

Designer to choose colors to be used in the design.

Requirements
Must have
• Just the logo on one side and details on the other
• Clean simple looking card
Nice to have
• Round corners and detail like raised or spot UV
• Something that stands out
Should not have
• To title needed, Director etc

```html
<!DOCTYPE html>
<html lang="en">
<head>
<meta charset="utf-8">
<title>Hartvale business card</title>
<link href="https://fonts.googleapis.com/css2?family=Jost:wght@400;500&display=swap" rel="stylesheet">
<style>
  :root {
    --backdrop: #e9e6e1;
    --card-white: #ffffff;
    --brand-blue: #1a5fa2;
    --navy: #1f2d6b;
    --ink-light: #ffffff;
  }
  * { box-sizing: border-box; margin: 0; padding: 0; }
  html, body {
    width: 1200px; height: 960px; overflow: hidden;
    background: var(--backdrop);
    font-family: "Jost", sans-serif;
  }
  .canvas {
    position: relative; width: 1200px; height: 960px;
  }
  .card {
    position: absolute; left: 240px;
    width: 720px; height: 412px;
    border-radius: 26px;
    box-shadow: 0 10px 28px rgba(0,0,0,0.18);
    overflow: hidden;
  }
  .card--front {
    top: 50px; background: var(--card-white);
    display: flex; align-items: center; justify-content: center;
  }
  .wordmark {
    font-size: 74px; font-weight: 400; letter-spacing: 2px;
    color: var(--brand-blue); line-height: 1;
    white-space: nowrap;
  }
  .card--back {
    top: 498px; background: var(--navy);
  }
  .contact {
    position: absolute; left: 46px; bottom: 40px;
    color: var(--ink-light);
  }
  .contact-name {
    font-size: 30px; font-weight: 400; margin-bottom: 12px;
    white-space: nowrap;
  }
  .contact-list { list-style: none; }
  .contact-item {
    display: flex; align-items: center; gap: 10px;
    font-size: 18px; line-height: 1.45;
    white-space: nowrap;
  }
  .contact-icon { width: 16px; height: 16px; flex: none; }
</style>
</head>
<body>
<main class="canvas">
  <section class="card card--front" aria-label="Card front">
    <span class="wordmark">HARTVALE</span>
  </section>

  <section class="card card--back" aria-label="Card back">
    <div class="contact">
      <p class="contact-name">Garrick Tenwood</p>
      <ul class="contact-list">
        <li class="contact-item">
          <svg class="contact-icon" viewBox="0 0 16 16" aria-hidden="true"><path fill="#fff" d="M3.2 1.5l2.3 2.6-1.3 1.6c.8 2.1 2.4 3.7 4.5 4.6l1.6-1.3 2.6 2.3-1.4 2.1C7 13.4 2.6 9 1.2 3z"/></svg>
          <span>0275390628</span>
        </li>
        <li class="contact-item">
          <svg class="contact-icon" viewBox="0 0 16 16" aria-hidden="true"><rect x="1" y="3.5" width="14" height="9.5" fill="#fff"/><path d="M1.5 4l6.5 5 6.5-5" fill="none" stroke="#1f2d6b" stroke-width="1.4"/></svg>
          <span>garrickt@hartvale.co.nz</span>
        </li>
        <li class="contact-item">
          <svg class="contact-icon" viewBox="0 0 16 16" aria-hidden="true"><circle cx="8" cy="8" r="7" fill="#fff"/><path d="M1 8h14M8 1c-3 3.5-3 10.5 0 14M8 1c3 3.5 3 10.5 0 14" fill="none" stroke="#1f2d6b" stroke-width="1.1"/></svg>
          <span>www.hartvale.co.nz</span>
        </li>
      </ul>
    </div>
  </section>
</main>
</body>
</html>
```